Re-Design an adult education portal

I need support to re-design an adult education portal. Currently the customer has an incomplete website which should be prepared in a new format.
I have the idea how to realize, but I have no clue how to design it. The hard thing is to have a "beautiful" website with available logo and main color. I hope you can support me.

Name of Website: moluvo (moluvo.ch)
Content: adult eduction for adult in safety at work, mountain climbing, dog school. various courses in different areas. But on old webpage is hard to find the different possibilities.
main color: Ral 6011 (green) -> #6C7C59
logo: you see on top of website the logo (2 dogs and a mountain with a colour gradient).

new website: for new webpage I decided to have a navigation for each section of education. In the main area I would like to have some pictures to give an idea what content is behind. At the moment it looks terrible, so I decided to use you as support for me to make the webpage prettier :). And maybe you have an better idea how to make it great. -> current state of new web page: https://moluvo.perch-net.ch/

Target Market(s)

adult eduction for adult in safety at work, mountain climbing, dog school

Number of Pages Required

1 page

Font styles to use
Serif
Sans Serif

Requirements
Must have
• As main color is set "Ral 6011" (green) -> #6C7C59

```html
<!DOCTYPE html>
<html lang="en">
<head>
<meta charset="utf-8">
<title>moluvo.ch – Adult Education</title>
<link rel="stylesheet" href="https://fonts.googleapis.com/css2?family=Bree+Serif&family=Arimo:wght@400&display=swap">
<style>
:root{
  --green:#6C7C59;
  --green-dark:#5B6A49;
  --ink:#2b2b2b;
  --text:#4a4a4a;
  --white:#ffffff;
  --footer:#121212;
}
*{margin:0;padding:0;box-sizing:border-box}
html,body{width:1200px;height:3563px;overflow:hidden}
body{position:relative;background:var(--white);font-family:"Arimo",Arial,sans-serif;color:var(--text)}
.serif{font-family:"Bree Serif",Georgia,serif}
.abs{position:absolute}
.hero{left:0;top:0;width:1200px;height:848px;background:linear-gradient(100deg,#4e5a52 0%,#3a4637 35%,#52503f 60%,#2f3a2c 100%)}
.header{left:0;top:51px;width:1200px;height:126px;background:rgba(255,255,255,.92)}
.brand{left:112px;top:88px;font-family:"Bree Serif",Georgia,serif;font-size:40px;color:var(--green);display:flex;align-items:center;gap:12px}
.brand .dot{width:22px;height:22px;border-radius:50%;background:var(--green)}
.nav{top:102px;left:398px;display:flex;gap:34px;font-family:"Bree Serif",Georgia,serif;font-size:17px;color:#555}
.hero-title{left:112px;top:442px;font-family:"Bree Serif",serif;font-size:58px;color:#fff}
.hero-sub{left:112px;top:516px;font-family:"Bree Serif",serif;font-size:18px;color:#fff}
.btn{display:flex;align-items:center;justify-content:center;border-radius:40px;font-family:"Bree Serif",serif;font-size:18px;color:#fff;background:var(--green)}
.btn-ghost{left:112px;top:570px;width:170px;height:58px;background:transparent;border:2px solid #fff}
h2{font-family:"Bree Serif",serif;font-weight:400;color:var(--ink)}
.about-title{left:112px;top:942px;font-size:52px}
.about-sub{left:112px;top:1010px;font-family:"Bree Serif",serif;font-size:17px;color:var(--green)}
.para{font-size:14px;line-height:25.6px;text-align:justify}
.about-text{left:112px;top:1052px;width:440px}
.about-btn{left:112px;top:1330px;width:173px;height:57px}
.about-photo{left:616px;top:942px;width:450px;height:450px;border-radius:50%;background:radial-gradient(circle at 50% 35%,#a9b27e,#6f8a3f 60%,#58742f)}
.courses{left:0;top:1489px;width:1200px;height:642px;background:var(--green-dark)}
.card{top:1553px;width:301px;height:499px;background:#fff;border-radius:3px;text-align:center}
.card .pic{position:absolute;left:10px;top:10px;width:281px;height:229px;border-radius:3px}
.card h3{position:absolute;left:0;right:0;top:263px;font-family:"Bree Serif",serif;font-weight:400;font-size:22px;color:var(--ink)}
.card .rule{position:absolute;left:128px;top:304px;width:45px;height:2px;background:var(--green)}
.card p{position:absolute;left:18px;right:18px;top:320px;font-size:13.5px;line-height:25.6px}
.card .btn{position:absolute;left:78px;top:418px;width:145px;height:50px}
.mountain{left:0;top:2131px;width:1200px;height:562px;background:linear-gradient(90deg,#f4dcc1 0%,#eccaa4 45%,#b98e68 75%,#7a5b3e 100%)}
.mt-title{left:112px;top:2268px;font-size:46px}
.rule-l{height:3px;background:var(--green)}
.mt-text{left:112px;top:2362px;width:509px;color:#333}
.mt-btn{left:112px;top:2519px;width:169px;height:59px}
.team-title{left:0;width:1200px;top:2742px;text-align:center;font-size:46px}
.face{width:214px;height:214px;border-radius:50%;top:2875px}
.member-name{top:2885px;font-family:"Bree Serif",serif;font-size:22px;color:var(--green)}
.member-text{top:2943px;width:218px;font-size:13.5px;line-height:25.6px}
.member-link{top:3064px;font-family:"Bree Serif",serif;font-size:16px;color:var(--green);text-decoration:underline}
.footer{left:0;top:3174px;width:1200px;height:389px;background:var(--footer)}
.foot-brand{left:0;width:1200px;top:3255px;display:flex;justify-content:center;align-items:center;gap:12px;font-family:"Bree Serif",serif;font-size:44px;color:#fff}
.foot-brand .dot{width:22px;height:22px;border-radius:50%;background:#fff}
.foot-nav{left:0;width:1200px;top:3382px;display:flex;justify-content:center;gap:34px;font-family:"Bree Serif",serif;font-size:17px;color:#fff}
.social{left:0;width:1200px;top:3432px;display:flex;justify-content:center;gap:10px}
.social span{width:36px;height:36px;border-radius:50%;border:2px solid #fff}
.copy{left:0;width:1200px;top:3494px;text-align:center;font-family:"Bree Serif",serif;font-size:14px;color:#fff}
</style>
</head>
<body>
<div class="abs hero" role="img" aria-label="Hiker with backpack and husky walking on a fallen log in a pine forest"></div>
<div class="abs header"></div>
<div class="abs brand"><span>moluvo.ch</span><span class="dot"></span></div>
<nav class="abs nav"><span>Occupational safety</span><span>First aid</span><span>dog school</span><span>CZV</span><span>Mountain training</span><span>moluvo</span></nav>
<div class="abs hero-title">Your Trainer</div>
<div class="abs hero-sub">Sed ut perspiciatis unde omnis iste natus error</div>
<a class="abs btn btn-ghost">Read More</a>

<h2 class="abs about-title">About us</h2>
<div class="abs about-sub">Anton &amp; Lea Brunner are there for you with passion</div>
<p class="abs para about-text">In my professional career, I have repeatedly experienced situations that gave me the idea of giving every interested person basic knowledge that would allow them to react correctly and with the necessary calm in an emergency. The pooling and combining of knowledge and skills from the various specialist areas gives people security and confidence in their actions. Our own experience has shown that the more professionally you are prepared for borderline situations, the more safely and successfully an &nbsp;can be mastered and even lives can be saved.Our course instructors are excellently trained: theoretically sound, tried and tested, methodically repeatedly and didactically trained.</p>
<a class="abs btn about-btn">Read More</a>
<div class="abs about-photo" role="img" aria-label="Couple sitting in a green meadow with two spaniel dogs"></div>

<div class="abs courses"></div>
<div class="abs card" style="left:112px">
  <div class="pic" role="img" aria-label="Hard hats and gloves in front of a construction site at sunset" style="background:linear-gradient(160deg,#5b5fa0,#c9926a 55%,#4a3a2a)"></div>
  <h3>Occupational safety</h3><div class="rule"></div>
  <p>Personal protective equipment against falls from a height &nbsp;sed ut perspiciatis unde omn is iste natus error sit voluptatem</p>
  <a class="btn">Read More</a>
</div>
<div class="abs card" style="left:451px">
  <div class="pic" role="img" aria-label="First aid course practising resuscitation on a training dummy" style="background:linear-gradient(160deg,#2f3848,#9a9a96 55%,#d8d2c4)"></div>
  <h3>First aid</h3><div class="rule"></div>
  <p>Personal protective equipment against falls from a height &nbsp;sed ut perspiciatis unde omn is iste natus error sit voluptatem</p>
  <a class="btn">Read More</a>
</div>
<div class="abs card" style="left:788px">
  <div class="pic" role="img" aria-label="Dog trainer with dogs lying on grass in a park" style="background:linear-gradient(180deg,#c9d6c2,#7ea044 55%,#4f7a2a)"></div>
  <h3>Dog School</h3><div class="rule"></div>
  <p>Personal protective equipment against falls from a height &nbsp;sed ut perspiciatis unde omn is iste natus error sit voluptatem</p>
  <a class="btn">Read More</a>
</div>

<div class="abs mountain" role="img" aria-label="Climber scaling a rock face against a hazy sunset sky"></div>
<h2 class="abs mt-title">Mountain Training</h2>
<div class="abs rule-l" style="left:112px;top:2337px;width:73px"></div>
<p class="abs para mt-text">Sed ut perspiciatis unde omnis iste natus error sit voluptatem accusantium dolo remque laudantium, totam rem aperiam, eaque ipsa quae ab illo inventore veritatis et quasi architecto beatae vitae dicta sunt explicabo. Nemo enim ipsam voluptatem quia voluptas sit aspernatur aut odit aut fugit, sed quia consequuntur magni dolores eos qui ratione voluptatem sequi nesciunt.</p>
<a class="abs btn mt-btn">Read More</a>

<h2 class="abs team-title">Our Team</h2>
<div class="abs rule-l" style="left:564px;top:2808px;width:72px"></div>

<div class="abs face" style="left:112px;background:linear-gradient(180deg,#8fa6c4,#c8ccd2 45%,#2f4a5a)" role="img" aria-label="Portrait of a mountain guide in front of snowy peaks"></div>
<div class="abs member-name" style="left:355px">Anton Brunner</div>
<div class="abs rule-l" style="left:355px;top:2926px;width:38px;height:2px"></div>
<p class="abs para member-text" style="left:355px">Certified mountain guide &amp; Snow sports instructor Qualified specialist in piste and rescue services &amp; Instr cable cars in Switzerland</p>
<a class="abs member-link" style="left:355px">Read More</a>

<div class="abs face" style="left:627px;background:linear-gradient(180deg,#3a3f4a,#8a8f99 50%,#e4e6ea)" role="img" aria-label="Portrait of a mountain guide in an orange jacket on a snowy summit"></div>
<div class="abs member-name" style="left:870px">Lea Brunner</div>
<div class="abs rule-l" style="left:870px;top:2926px;width:38px;height:2px"></div>
<p class="abs para member-text" style="left:870px">Certified mountain guide &amp; Snow sports instructor Qualified specialist in piste and rescue services &amp; Instr cable cars in Switzerland</p>
<a class="abs member-link" style="left:870px">Read More</a>

<footer class="abs footer"></footer>
<div class="abs foot-brand"><span>moluvo.ch</span><span class="dot"></span></div>
<nav class="abs foot-nav"><span>Occupational safety</span><span>First aid</span><span>dog school</span><span>CZV</span><span>Mountain training</span><span>moluvo</span></nav>
<div class="abs social" aria-label="Social media links"><span></span><span></span><span></span></div>
<div class="abs copy">© Copyright 2021 moluvo.All Rights Reserved.</div>
</body>
</html>
```